Clearing Your Slate - Banner Ad for TH Website

I need a banner ad for a book I'm selling.

The book is about Clearing Your Slate, that is a County Court Judgment, from a credit report.

I have two websites. I want the banner ad to appear on
www.thorncaldwell.co.uk

It will then link to the new site: https://debtslatecleaner.co.uk/

The first site already has a lot of traffic from visitors wanting to remove a CCJ. The purpose of that first site was originally for visitors to become clients of the law firm. However, most visitors can't afford legal advice and so I'd like to offer them the book instead.

I would like to see designs that use the colour green. The final design should communicate financial freedom, simplicity and trustworthiness.

Target Market(s)

Individuals who have discovered a CCJ on their credit report

Industry/Entity Type

Law

Font styles to use
Sans Serif

Colors
0054AA
0677BA
7BADD7
CADEEF
E8F1F8
0094D4
00A9DD
6FCCEA
C7EBF8
E9F6FB
00AB8E
00BBA5
67D7C9
C6EFE9
E9F9F6

Requirements
Must have
• Must fit at the end of a blog article, such as this one https://www.thorncaldwell.co.uk/ccj-wrong-address/

```html
<!DOCTYPE html>
<html lang="en">
<head>
<meta charset="utf-8">
<title>Clearing Your Slate – Banner Ads</title>
<link rel="stylesheet" href="https://fonts.googleapis.com/css2?family=Montserrat:wght@700;800&display=swap">
<style>
  :root {
    --stage: #8c8c8c;
    --green-deep: #43a047;
    --green-mid: #4fb052;
    --green-shadow: #2a6e2d;
    --green-pale: #c8fba6;
    --green-olive: #7cad4a;
    --gold: #ecc97a;
    --gold-soft: #d9d27e;
    --cta: #e32b2b;
    --white: #ffffff;
    --url: #2e7d32;
  }
  * { margin: 0; padding: 0; box-sizing: border-box; }
  html, body { width: 1200px; height: 870px; overflow: hidden; }
  body {
    background: var(--stage);
    font-family: "Montserrat", Arial, sans-serif;
    position: relative;
  }
  .banner { position: absolute; overflow: hidden; }
  .banner__bg { position: absolute; inset: 0; width: 100%; height: 100%; }
  .headline, .subline { position: absolute; left: 0; color: var(--white); text-align: center; font-weight: 800;
    text-shadow: 2px 2px 0 var(--green-shadow); line-height: 1; }
  .cta {
    position: absolute; display: flex; align-items: center; justify-content: center;
    background: var(--cta); color: var(--white); border: 2px solid var(--white);
    border-radius: 40px; font-weight: 800; text-decoration: none; white-space: nowrap;
  }
  .product-shot { position: absolute; border-radius: 4px;
    background: linear-gradient(135deg, #f4f4f4 0%, #e2e2e2 55%, #cfcfcf 100%); }

  /* Leaderboard */
  .banner--wide { left: 85px; top: 305px; width: 777px; height: 320px; }
  .banner--wide .headline--lead { top: 28px; width: 440px; font-size: 34px; }
  .banner--wide .headline--main { top: 55px; width: 440px; font-size: 62px; letter-spacing: -1px; }
  .banner--wide .headline--ccj { top: 116px; width: 440px; font-size: 64px; }
  .banner--wide .headline--ccj small { font-size: 32px; }
  .banner--wide .subline { top: 194px; width: 440px; font-size: 22px; line-height: 27px; }
  .banner--wide .cta { left: 86px; top: 257px; width: 273px; height: 35px; font-size: 20px; }
  .banner--wide .product-shot { left: 422px; top: 25px; width: 312px; height: 270px; }

  /* Skyscraper */
  .banner--tall { left: 929px; top: 97px; width: 196px; height: 686px; }
  .banner--tall .headline--lead { top: 70px; width: 196px; font-size: 22px; }
  .banner--tall .headline--main { top: 89px; width: 196px; font-size: 38px; letter-spacing: -.5px; }
  .banner--tall .headline--ccj { top: 129px; width: 196px; font-size: 42px; }
  .banner--tall .headline--ccj small { font-size: 21px; }
  .banner--tall .subline { top: 201px; width: 196px; font-size: 17px; line-height: 22.5px; }
  .banner--tall .cta { left: 16px; top: 307px; width: 164px; height: 22px; font-size: 12.5px; }
  .banner--tall .product-shot { left: 8px; top: 393px; width: 181px; height: 158px; }
  .banner--tall .site-url { position: absolute; left: 0; top: 626px; width: 196px; text-align: center;
    color: var(--url); font-weight: 800; font-size: 10px; }
</style>
</head>
<body>

<section class="banner banner--wide" aria-label="Leaderboard banner">
  <svg class="banner__bg" viewBox="0 0 777 320" preserveAspectRatio="none" aria-hidden="true">
    <defs>
      <linearGradient id="stripeWide" x1="0" y1="0" x2="1" y2="1">
        <stop offset="0" stop-color="var(--gold)"/>
        <stop offset="1" stop-color="var(--gold-soft)" stop-opacity="0.4"/>
      </linearGradient>
    </defs>
    <rect width="777" height="320" fill="var(--green-pale)"/>
    <polygon points="385,0 440,0 640,320 585,320" fill="url(#stripeWide)"/>
    <polygon points="0,0 385,0 578,320 0,320" fill="var(--green-deep)"/>
    <polygon points="0,130 190,320 0,320" fill="var(--green-mid)"/>
  </svg>
  <p class="headline headline--lead">Need to</p>
  <p class="headline headline--main">Remove</p>
  <p class="headline headline--ccj"><small>a</small>CCJ?</p>
  <p class="subline">Find out how with this simple<br>jargon-free guide</p>
  <a class="cta" href="https://debtslatecleaner.co.uk/">Get Your Copy Now</a>
  <div class="product-shot" role="img" aria-label="Clearing Your Slate book shown as paperback, tablet and phone editions"></div>
</section>

<section class="banner banner--tall" aria-label="Skyscraper banner">
  <svg class="banner__bg" viewBox="0 0 196 686" preserveAspectRatio="none" aria-hidden="true">
    <defs>
      <linearGradient id="stripeTall" x1="0" y1="0" x2="1" y2="1">
        <stop offset="0" stop-color="var(--gold)"/>
        <stop offset="1" stop-color="var(--gold-soft)" stop-opacity="0.3"/>
      </linearGradient>
    </defs>
    <rect width="196" height="686" fill="var(--green-pale)"/>
    <polygon points="0,250 196,540 196,640 0,330" fill="url(#stripeTall)"/>
    <polygon points="0,0 196,0 196,540 0,250" fill="var(--green-deep)"/>
    <polygon points="0,0 60,0 0,40" fill="var(--green-mid)"/>
    <polygon points="130,560 196,560 196,670" fill="var(--green-olive)"/>
  </svg>
  <p class="headline headline--lead">Need to</p>
  <p class="headline headline--main">Remove</p>
  <p class="headline headline--ccj"><small>a</small>CCJ?</p>
  <p class="subline">Find out how<br>with this simple<br>jargon-free<br>guide</p>
  <a class="cta" href="https://debtslatecleaner.co.uk/">Get Your Copy Now</a>
  <div class="product-shot" role="img" aria-label="Clearing Your Slate book shown as paperback, tablet and phone editions"></div>
  <p class="site-url">debtslatecleaner.co.uk</p>
</section>

</body>
</html>
```